Maple Gable Business Card

Colors can be blue, grey and white as you see in the attached logo. Needs to have a spot for name, title, phone, email, address, and website. There also needs to be a spot for an agent's picture.

Contact Information for Business Card

See project description.

Colors

Designer to choose colors to be used in the design.

```html
<!DOCTYPE html>
<html lang="en">
<head>
<meta charset="utf-8">
<title>Maple Gable Business Card</title>
<link rel="stylesheet" href="https://fonts.googleapis.com/css2?family=Montserrat:wght@500;600&family=Mulish:wght@400;500&display=swap">
<style>
  :root {
    --stage: #1c1c1c;
    --stage-edge: #0e0e0e;
    --brand-blue: #2f74b8;
    --card-dark: #262626;
    --card-dark-edge: #1b1b1b;
    --card-light: #ffffff;
    --ink: #3a3a3a;
    --ink-soft: #555555;
    --rule: #4f8fcc;
    --photo-top: #e4e9ef;
    --photo-bottom: #c9d3de;
  }
  * { box-sizing: border-box; margin: 0; padding: 0; }
  html, body { width: 1200px; height: 900px; overflow: hidden; }
  body {
    background: radial-gradient(ellipse at 50% 40%, var(--stage) 0%, var(--stage-edge) 100%);
    font-family: "Mulish", sans-serif;
    position: relative;
  }
  .card {
    position: absolute;
    left: 290px;
    width: 620px;
    height: 354px;
    border-radius: 4px;
    overflow: hidden;
    box-shadow: 0 18px 40px rgba(0,0,0,.55);
  }
  .card--back {
    top: 70px;
    background: linear-gradient(135deg, var(--card-dark) 0%, var(--card-dark-edge) 100%);
    display: flex;
    align-items: center;
    justify-content: center;
  }
  .card--front {
    top: 470px;
    background: var(--card-light);
  }
  .brand-name {
    font-family: "Montserrat", sans-serif;
    font-weight: 600;
    color: var(--brand-blue);
    text-transform: uppercase;
    letter-spacing: 1px;
    white-space: nowrap;
  }
  .card--back .brand-name { font-size: 44px; }
  .card--front .brand {
    position: absolute;
    left: 44px;
    top: 58px;
  }
  .card--front .brand-name { font-size: 30px; }
  .agent-photo {
    position: absolute;
    left: 44px;
    top: 112px;
    width: 104px;
    height: 128px;
    border-radius: 3px;
    background: linear-gradient(180deg, var(--photo-top) 0%, var(--photo-bottom) 100%);
    border: 1px solid var(--rule);
  }
  .details {
    position: absolute;
    left: 352px;
    top: 56px;
    width: 240px;
    color: var(--ink);
  }
  .agent-name {
    font-family: "Montserrat", sans-serif;
    font-weight: 600;
    font-size: 20px;
    color: var(--brand-blue);
    letter-spacing: 1px;
    text-transform: uppercase;
    line-height: 1.1;
    white-space: nowrap;
  }
  .agent-title {
    font-size: 14px;
    color: var(--ink-soft);
    margin-top: 2px;
  }
  .rule {
    height: 1px;
    background: var(--rule);
    margin: 10px 0;
  }
  .address {
    font-size: 15px;
    line-height: 1.45;
    font-style: normal;
  }
  .contact-list { list-style: none; font-size: 15px; line-height: 1.6; }
  .contact-list li { display: flex; align-items: center; gap: 8px; }
  .contact-list svg { width: 12px; height: 12px; flex: none; }
  .band {
    position: absolute;
    left: 0;
    bottom: 0;
    width: 620px;
    height: 80px;
  }
  .website {
    position: absolute;
    left: 150px;
    bottom: 22px;
    display: flex;
    align-items: center;
    gap: 10px;
    color: var(--card-light);
    font-size: 15px;
    letter-spacing: .5px;
  }
  .website-mark {
    width: 11px;
    height: 11px;
    background: var(--card-light);
  }
</style>
</head>
<body>
  <section class="card card--back" aria-label="Card back">
    <p class="brand-name">Maple Gable</p>
  </section>

  <section class="card card--front" aria-label="Card front">
    <div class="brand">
      <p class="brand-name">Maple Gable</p>
    </div>

    <div class="agent-photo" role="img" aria-label="Agent portrait photo"></div>

    <div class="details">
      <h1 class="agent-name">Daniel Morrow</h1>
      <p class="agent-title">Director</p>
      <div class="rule"></div>
      <address class="address">218 Cedar Hollow Drive<br>Reno, NV 89501</address>
      <div class="rule"></div>
      <ul class="contact-list">
        <li>
          <svg viewBox="0 0 12 12" aria-hidden="true"><path d="M3 1 L5 3.5 L4 5 Q5 7 7 8 L8.5 7 L11 9 L9.5 11 Q5 11 1 5 Q1 2 3 1 Z" fill="var(--brand-blue)"/></svg>
          (555) 214-3380
        </li>
        <li>
          <svg viewBox="0 0 12 12" aria-hidden="true"><rect x="0.75" y="2.25" width="10.5" height="7.5" fill="none" stroke="var(--brand-blue)" stroke-width="1.2"/><path d="M1 2.5 L6 6.5 L11 2.5" fill="none" stroke="var(--brand-blue)" stroke-width="1.2"/></svg>
          info@maplegable.com
        </li>
      </ul>
    </div>

    <svg class="band" viewBox="0 0 620 80" preserveAspectRatio="none" aria-hidden="true">
      <polygon points="0,4 262,12 620,80 0,80" fill="var(--brand-blue)"/>
    </svg>
    <p class="website"><span class="website-mark"></span>www.maplegable.com</p>
  </section>
</body>
</html>
```